Bramblewood Card Company Business Cards

We are a trading card store with Glimmorax, sports and other TCG cards, we need a business card design that encompasses a clean cut, modern style with a retro flare. website is bramblewoodcardco.com for reference. Can utilize a comic book era feel or a more modern outdoor feel to utilize the "Pacific Northwest" elements of tress, mountains, etc.

Industry/Entity Type

Trading cards and collectibles

Contact Information for Business Card

business name, email address, phone number, name, owner job title

Font styles to use
Sans Serif

```html
<!DOCTYPE html>
<html lang="en">
<head>
<meta charset="utf-8">
<title>Bramblewood Card Company – Business Cards</title>
<link href="https://fonts.googleapis.com/css2?family=Montserrat:wght@400;500;700;800&display=swap" rel="stylesheet">
<style>
  :root {
    --stage: #232323;
    --card-white: #ffffff;
    --brand-cyan: #1fbde0;
    --brand-cyan-deep: #17a9cb;
    --ink: #3a3a3a;
    --slate: #6b6b6b;
    --swoosh-grey: #c4c4c4;
    --shadow: rgba(0,0,0,0.45);
  }
  * { box-sizing: border-box; margin: 0; padding: 0; }
  html, body { width: 1200px; height: 801px; overflow: hidden; }
  body {
    background: var(--stage);
    font-family: "Montserrat", sans-serif;
    position: relative;
  }
  .card {
    position: absolute;
    top: 246px;
    width: 540px;
    height: 309px;
    border-radius: 18px;
    overflow: hidden;
    box-shadow: 0 14px 30px var(--shadow);
  }
  .card--front { left: 50px; background: var(--card-white); }
  .card--back { left: 610px; background: var(--brand-cyan); }

  .front-swoosh { position: absolute; inset: 0; }

  .accent-tab {
    position: absolute;
    left: 0;
    top: 76px;
    width: 34px;
    height: 22px;
    background: var(--brand-cyan);
  }
  .identity {
    position: absolute;
    left: 60px;
    top: 56px;
  }
  .identity__name {
    font-weight: 800;
    font-size: 25px;
    letter-spacing: 1px;
    color: var(--brand-cyan);
    text-transform: uppercase;
    line-height: 1;
  }
  .identity__role {
    font-weight: 400;
    font-size: 14px;
    color: var(--ink);
    margin-top: 5px;
  }

  .contact {
    position: absolute;
    left: 60px;
    top: 150px;
    font-size: 13px;
    color: var(--ink);
    line-height: 1.45;
    list-style: none;
  }
  .contact__address { margin-bottom: 12px; }
  .contact li { display: flex; align-items: center; gap: 8px; }
  .contact svg { width: 12px; height: 12px; flex: none; }

  .brand-mark {
    position: absolute;
    right: 40px;
    top: 42px;
    width: 180px;
    display: flex;
    align-items: center;
    gap: 8px;
  }
  .brand-mark__square {
    width: 14px; height: 14px; flex: none;
    background: var(--slate);
  }
  .brand-mark__name {
    font-weight: 700;
    font-size: 15px;
    line-height: 1.2;
    color: var(--slate);
    text-transform: uppercase;
    letter-spacing: 0.5px;
  }

  .back-brand {
    position: absolute;
    inset: 0;
    display: flex;
    align-items: center;
    justify-content: center;
    gap: 12px;
  }
  .back-brand__square {
    width: 22px; height: 22px; flex: none;
    background: var(--ink);
    opacity: 0.85;
  }
  .back-brand__name {
    font-weight: 800;
    font-size: 26px;
    line-height: 1.15;
    color: var(--ink);
    text-transform: uppercase;
    letter-spacing: 1px;
    opacity: 0.85;
  }
</style>
</head>
<body>
  <section class="card card--front" aria-label="Business card front">
    <svg class="front-swoosh" viewBox="0 0 540 309" preserveAspectRatio="none" aria-hidden="true">
      <path d="M540 150 C420 195 290 250 238 309 L540 309 Z" fill="var(--swoosh-grey)"/>
      <path d="M540 160 C430 200 300 250 250 309 L540 309 Z" fill="var(--brand-cyan)"/>
    </svg>

    <span class="accent-tab" aria-hidden="true"></span>

    <div class="identity">
      <h1 class="identity__name">Corwin Hale</h1>
      <p class="identity__role">CEO/Founder</p>
    </div>

    <ul class="contact">
      <li class="contact__address">P.O. Box 3870 Lane<br>Region Name CD 6173</li>
      <li>
        <svg viewBox="0 0 12 12" aria-hidden="true"><path d="M3 1 L5 3 L4 5 Q5 7 7 8 L9 7 L11 9 L9.5 11 Q4 10 1 3 Z" fill="var(--brand-cyan)"/></svg>
        (555) 014 2368
      </li>
      <li>
        <svg viewBox="0 0 12 12" aria-hidden="true"><rect x="1" y="2.5" width="10" height="7" fill="var(--brand-cyan)"/><path d="M1 2.5 L6 6.5 L11 2.5" stroke="#fff" fill="none"/></svg>
        info@bramblewoodcardco.com
      </li>
      <li>
        <svg viewBox="0 0 12 12" aria-hidden="true"><circle cx="6" cy="6" r="5" fill="none" stroke="var(--brand-cyan)" stroke-width="1.3"/><path d="M1 6 H11 M6 1 V11" stroke="var(--brand-cyan)"/></svg>
        www.bramblewoodcardco.com
      </li>
    </ul>

    <div class="brand-mark">
      <span class="brand-mark__square"></span>
      <span class="brand-mark__name">Bramblewood Card Company</span>
    </div>
  </section>

  <section class="card card--back" aria-label="Business card back">
    <div class="back-brand">
      <span class="back-brand__square"></span>
      <span class="back-brand__name">Bramblewood<br>Card Company</span>
    </div>
  </section>
</body>
</html>
```